Bookmarks for teachers and high school students - Range of 6

We are after a range of 6 bookmarks to use as hand outs to schools and students that we supply books and other school resources to.

Each bookmark is to have an inspirational quote on it and be a different color. You can decide color and background texture.

The back of them shall all be black or white, so just fronts needed. We want these 6 bookmarks to be similar in design, so they look like a matching range. And be nice enough that teachers and students will pick one to use.

We also want our logo to be on the bookmark, maybe just tucked down the bottom and our web address showing please - www.larkvale.com.au

Attached is the 6 quotes we want to use and an examples of the type of font I would like to see. But each a different font ..Also attached is our logo.

I think simple and smart may be best, but see what you come up with as I am also open to making them funky for students (if possible)

The print size of each bookmark is 40mm by 210mm

Target Market(s)

teachers and high school students

Industry/Entity Type

School

Requirements
Must have
• be eye catching

```html
<!DOCTYPE html>
<html lang="en">
<head>
<meta charset="utf-8">
<title>Larkvale Bookmark Range</title>
<link rel="stylesheet" href="https://fonts.googleapis.com/css2?family=Bebas+Neue&family=Josefin+Sans:wght@300;400&family=Libre+Baskerville&family=Montserrat:wght@600&family=Oswald:wght@400;600;700&family=Yesteryear&display=swap">
<style>
:root{
  --canvas:#ecebe8;
  --paper:#ffffff;
  --ink:#2a2a2a;
  --purple-a:#4f3a92;--purple-b:#8e6bc7;--purple-band:#6a4ea5;
  --night-a:#0c1a2e;--night-b:#1e5c86;--night-band:#333333;
  --amber-a:#d9541b;--amber-b:#f7a21a;--amber-band:#e2661c;
  --forest-a:#1e3a22;--forest-b:#4d9a3a;--forest-band:#2a5a2e;
  --ocean-a:#0b4a6e;--ocean-b:#3aa2c8;--ocean-band:#0f3e5a;
  --magenta-a:#d4157e;--magenta-b:#5a2a7a;--magenta-band:#d4157e;
  --light:#ffffff;
  --blush:#f6d9f0;
  --gold:#ffe27a;
  --sand:#e8dfb8;
}
*{margin:0;padding:0;box-sizing:border-box}
html,body{width:1200px;height:729px;overflow:hidden;background:var(--canvas)}
.range{position:relative;width:1200px;height:729px}
.bookmark{position:absolute;top:47px;width:117px;height:610px;display:flex;flex-direction:column;box-shadow:0 2px 8px rgba(0,0,0,.25)}
.art{position:relative;height:518px;overflow:hidden}
.quote{position:absolute;left:0;right:0;display:flex;flex-direction:column;align-items:center;text-align:center;line-height:1}
.credit{position:absolute;bottom:8px;left:0;right:0;text-align:center;font:9px/1.15 "Libre Baskerville",serif;color:var(--light)}
.brand{height:65px;background:var(--paper);display:flex;align-items:center;justify-content:center}
.brand-name{font:400 18px "Josefin Sans",sans-serif;color:var(--ink)}
.url{height:27px;display:flex;align-items:center;justify-content:center;font:600 8px "Montserrat",sans-serif;color:var(--light)}
.script{font-family:"Yesteryear",cursive}
.condensed{font-family:"Oswald",sans-serif}
.thin{font-family:"Josefin Sans",sans-serif;font-weight:300}
.display{font-family:"Bebas Neue",sans-serif}
.ribbon{display:inline-block;padding:2px 10px;margin:3px 0}

.bm-magic{left:162px}
.bm-magic .art{background:radial-gradient(ellipse at 60% 70%,var(--purple-b),var(--purple-a) 75%)}
.bm-magic .quote{top:130px;color:var(--blush)}
.bm-magic .url{background:var(--purple-band)}

.bm-plan{left:313px}
.bm-plan .art{background:linear-gradient(175deg,var(--night-b) 0%,var(--night-a) 55%,#05080e 100%)}
.bm-plan .quote{top:125px;color:#cfe8ff}
.bm-plan .url{background:var(--night-band)}

.bm-together{left:465px}
.bm-together .art{background:linear-gradient(180deg,var(--amber-a),var(--amber-b) 70%,#fbc23a)}
.bm-together .quote{top:128px;color:var(--gold)}
.bm-together .url{background:var(--amber-band)}

.bm-tree{left:619px}
.bm-tree .art{background:linear-gradient(180deg,var(--forest-a) 0%,#2f5a2a 45%,var(--forest-b) 75%,#2b4a22 100%)}
.bm-tree .quote{top:78px;color:#e7f1d8}
.bm-tree .url{background:var(--forest-band)}

.bm-logic{left:769px}
.bm-logic .art{background:linear-gradient(180deg,#1b6e96 0%,var(--ocean-b) 40%,var(--ocean-a) 85%,#0a3550 100%)}
.bm-logic .quote{top:130px;color:var(--light)}
.bm-logic .url{background:var(--ocean-band)}
.bm-logic .ribbon{background:#e9f3f8;color:var(--ocean-a)}

.bm-dreams{left:919px}
.bm-dreams .art{background:linear-gradient(160deg,var(--magenta-a) 0%,#b0188a 45%,var(--magenta-b) 100%)}
.bm-dreams .quote{top:130px;color:var(--light)}
.bm-dreams .url{background:var(--magenta-band)}
.bm-dreams .ribbon{background:var(--light);color:var(--magenta-a)}
</style>
</head>
<body>
<main class="range">

  <article class="bookmark bm-magic">
    <div class="art" role="img" aria-label="Violet background with soft glowing light streaks">
      <div class="quote">
        <span class="script" style="font-size:17px">“Those that</span>
        <span class="condensed" style="font-size:15px;margin-top:4px">DON'T BELIEVE</span>
        <span class="condensed" style="font-size:10px;margin-top:3px">— IN —</span>
        <span class="condensed" style="font-size:38px;font-weight:600">MAGIC</span>
        <span class="script" style="font-size:21px">will never</span>
        <span class="condensed" style="font-size:40px;font-weight:600;margin-top:2px">FIND</span>
        <span class="condensed" style="font-size:40px;font-weight:600">IT”</span>
      </div>
    </div>
    <div class="brand"><span class="brand-name">Larkvale</span></div>
    <div class="url">www.larkvale.com.au</div>
  </article>

  <article class="bookmark bm-plan">
    <div class="art" role="img" aria-label="Dark night city scene with glowing embers">
      <div class="quote">
        <span class="thin" style="font-size:15px">“DOESN'T</span>
        <span class="thin" style="font-size:15px">MATTER</span>
        <span class="thin" style="font-size:30px;font-weight:400;margin-top:4px">WHO</span>
        <span class="thin" style="font-size:25px;font-weight:400">WE ARE</span>
        <span style="width:80px;height:1px;background:#cfe8ff;margin:8px 0"></span>
        <span class="thin" style="font-size:16px">WHAT</span>
        <span class="thin" style="font-size:16px">MATTERS</span>
        <span class="thin" style="font-size:28px;font-weight:400;margin-top:3px">IS OUR</span>
        <span class="thin" style="font-size:28px;font-weight:400">PLAN”</span>
      </div>
      <p class="credit">The Quiet<br>Harbour</p>
    </div>
    <div class="brand"><span class="brand-name">Larkvale</span></div>
    <div class="url">www.larkvale.com.au</div>
  </article>

  <article class="bookmark bm-together">
    <div class="art" role="img" aria-label="Warm orange glow with soft light rays">
      <div class="quote">
        <span class="script" style="font-size:21px">“Coming</span>
        <span class="condensed" style="font-size:17px;font-weight:700">TOGETHER IS</span>
        <span class="condensed" style="font-size:17px;font-weight:700">A BEGINNING;</span>
        <span class="script" style="font-size:21px;margin-top:4px">Keeping</span>
        <span class="condensed" style="font-size:17px;font-weight:700">TOGETHER IS</span>
        <span class="condensed" style="font-size:17px;font-weight:700">PROGRESS;</span>
        <span class="script" style="font-size:21px;margin-top:4px">Working</span>
        <span class="condensed" style="font-size:17px;font-weight:700">TOGETHER IS</span>
        <span class="condensed" style="font-size:17px;font-weight:700">SUCCESS”</span>
      </div>
      <p class="credit">Walter Brand</p>
    </div>
    <div class="brand"><span class="brand-name">Larkvale</span></div>
    <div class="url">www.larkvale.com.au</div>
  </article>

  <article class="bookmark bm-tree">
    <div class="art" role="img" aria-label="Green scene of a young tree held in cupped hands">
      <div class="quote">
        <span class="thin" style="font-size:15px">“The best</span>
        <span class="thin" style="font-size:15px">time to plant</span>
        <span class="display" style="font-size:36px;margin-top:3px">A TREE</span>
        <span class="thin" style="font-size:10px;font-weight:400">was 20 years ago</span>
        <span class="thin" style="font-size:14px;margin-top:8px">The second</span>
        <span class="ribbon thin" style="background:var(--sand);color:var(--forest-a);font-size:16px;font-weight:400;width:117px">best time</span>
        <span class="thin" style="font-size:16px">is <span class="display" style="font-size:22px">NOW”</span></span>
      </div>
      <p class="credit">Chinese Proverb</p>
    </div>
    <div class="brand"><span class="brand-name">Larkvale</span></div>
    <div class="url">www.larkvale.com.au</div>
  </article>

  <article class="bookmark bm-logic">
    <div class="art" role="img" aria-label="Blue misty window with soft moonlight">
      <div class="quote">
        <span class="script" style="font-size:24px">“Logic</span>
        <span class="ribbon script" style="font-size:15px">will get</span>
        <span class="script" style="font-size:13px">you</span>
        <span class="thin" style="font-size:14px;font-weight:400;margin-top:3px">from A to Z</span>
        <span class="display" style="font-size:24px;margin-top:6px">IMAGINATION</span>
        <span class="ribbon script" style="font-size:15px">will get</span>
        <span class="script" style="font-size:13px">you</span>
        <span class="script" style="font-size:19px">everywhere”</span>
      </div>
      <p class="credit">Otto Lindqvist</p>
    </div>
    <div class="brand"><span class="brand-name">Larkvale</span></div>
    <div class="url">www.larkvale.com.au</div>
  </article>

  <article class="bookmark bm-dreams">
    <div class="art" role="img" aria-label="Magenta and violet painted texture">
      <div class="quote">
        <span class="script" style="font-size:19px">All our</span>
        <span class="condensed" style="font-size:24px;font-weight:700">DREAMS</span>
        <span class="script" style="font-size:14px">can come true</span>
        <span class="ribbon condensed" style="font-size:11px;font-weight:600">IF WE HAVE THE</span>
        <span class="condensed" style="font-size:26px;font-weight:700">COURAGE</span>
        <span class="condensed" style="font-size:14px;font-weight:600">TO PURSUE</span>
        <span class="condensed" style="font-size:14px;font-weight:600">THEM”</span>
      </div>
    </div>
    <div class="brand"><span class="brand-name">Larkvale</span></div>
    <div class="url">www.larkvale.com.au</div>
  </article>

</main>
</body>
</html>
```